Business card design for Kelvo Engineering Tandem

We need a new business card design along with all the necessary to place an order. The company is Kelvo Engineering Tandem and we recently updated our logo.

```html
<!DOCTYPE html>
<html lang="en">
<head>
<meta charset="utf-8">
<title>Kelvo Engineering Tandem – Business Card</title>
<link href="https://fonts.googleapis.com/css2?family=Kanit:wght@400;500;600&display=swap" rel="stylesheet">
<style>
  :root {
    --page: #2b2b2d;
    --card: #141414;
    --yellow: #e4bd24;
    --silver: #9c9c9c;
    --light: #f2f2f2;
    --back-silver: #c8c8c8;
  }
  * { margin: 0; padding: 0; box-sizing: border-box; }
  html, body { width: 1200px; height: 1059px; overflow: hidden; }
  body {
    background: var(--page);
    font-family: "Kanit", sans-serif;
    position: relative;
  }
  .card {
    position: absolute;
    width: 690px;
    height: 394px;
    background: var(--card);
    border-radius: 26px;
    overflow: hidden;
  }
  .card--front { left: 256px; top: 100px; }
  .card--back { left: 253px; top: 536px; width: 694px; height: 396px; }

  .brand__mark { position: absolute; }
  .brand__name, .brand__sub {
    position: absolute;
    font-weight: 600;
    text-transform: uppercase;
    line-height: 1;
    white-space: nowrap;
  }

  .card--front .brand__mark { left: 105px; top: 48px; width: 96px; height: 96px; background: var(--yellow); }
  .card--front .brand__name { left: 238px; top: 13px; font-size: 105px; color: var(--silver); letter-spacing: 1px; }
  .card--front .brand__sub { left: 238px; top: 115px; font-size: 34px; color: var(--silver); letter-spacing: 1px; }

  .person {
    position: absolute;
    right: 389px;
    top: 199px;
    text-align: right;
  }
  .person__name {
    color: var(--yellow);
    font-weight: 600;
    font-size: 38px;
    line-height: 1;
  }
  .person__title {
    color: var(--light);
    font-size: 18px;
    line-height: 1;
    font-weight: 400;
    margin-top: 3px;
  }
  .divider {
    position: absolute;
    left: 329px;
    top: 200px;
    width: 2px;
    height: 70px;
    background: var(--yellow);
  }
  .contacts {
    position: absolute;
    left: 356px;
    top: 193px;
    list-style: none;
  }
  .contacts li {
    display: flex;
    align-items: center;
    gap: 9px;
    height: 27.5px;
    color: var(--light);
    font-size: 18.5px;
    white-space: nowrap;
  }
  .contacts svg { width: 15px; height: 15px; fill: var(--yellow); flex: none; }

  .address-band {
    position: absolute;
    left: 0;
    top: 339px;
    width: 100%;
    height: 24px;
    background: var(--yellow);
    color: var(--light);
    font-size: 17.5px;
    line-height: 24px;
    padding-left: 61px;
    white-space: nowrap;
  }

  .card--back .brand__mark { left: 82px; top: 150px; width: 110px; height: 110px; background: var(--back-silver); }
  .card--back .brand__name { left: 228px; top: 112px; font-size: 115px; color: var(--back-silver); letter-spacing: 1px; }
  .card--back .brand__sub { left: 230px; top: 226px; font-size: 36px; color: var(--back-silver); letter-spacing: 1px; }
</style>
</head>
<body>
  <section class="card card--front">
    <span class="brand__mark"></span>
    <p class="brand__name">Kelvo</p>
    <p class="brand__sub">Engineering Tandem</p>

    <div class="person">
      <p class="person__name">DANIEL MARSH</p>
      <p class="person__title">Managing Director</p>
    </div>
    <div class="divider"></div>

    <ul class="contacts">
      <li>
        <svg viewBox="0 0 16 16" aria-hidden="true"><path d="M1 6c0-2 3-3 7-3s7 1 7 3v1h-3V5.5C10.5 5 5.5 5 4 5.5V7H1z"/><path d="M4 8h8l2 6H2z"/></svg>
        01632 960418
      </li>
      <li>
        <svg viewBox="0 0 16 16" aria-hidden="true"><path d="M1 3h14v2L8 9 1 5z"/><path d="M1 7l7 4 7-4v6H1z"/></svg>
        sales@kelvoengineering.co.uk
      </li>
      <li>
        <svg viewBox="0 0 16 16" aria-hidden="true"><circle cx="8" cy="8" r="7"/></svg>
        www.kelvoengineering.co.uk
      </li>
    </ul>

    <div class="address-band">Kelvo Engineering Tandem 22b Harlow Close, Kettering NN15 4TD</div>
  </section>

  <section class="card card--back">
    <span class="brand__mark"></span>
    <p class="brand__name">Kelvo</p>
    <p class="brand__sub">Engineering Tandem</p>
  </section>
</body>
</html>
```